Creation of a construction/bricklaying business website

Following the template format of "Halloway 7", the following content would need to be included:
1. Landing page with 3 tiles that go to their own pages.
- Landing page to include background photo and description of services offered.
2. 3 tiles to include:
a) "Contact Us For A Free Quote or Friendly Discussion" Form (middle tile)
b) Case Studies and Testimonials
c) Certifications and Professional Membership
- Design logo to be used from previous SketchNestle project. Example of logo attached below, please access full JPG files from our account.

Target Market(s)

Prospective clients seeking construction work (bricklaying speciality)

Industry/Entity Type

Residential Construction

Coding

Coded - Design and coding required

Number of Pages Required

4 page

Font styles to use
Sans Serif

Colors

Designer to choose colors to be used in the design.

Requirements
Must have
• Following the template format of "Halloway 7", the following content would need to be included:
• 1. Landing parent page with 3 tiles that go to the 3 child pages.
• - Landing page to include background photo and description of services offered.
• 2. 3 tiles to include:
• a) "Contact Us For A Free Quote or Friendly Discussion" Form (middle tile)
• b) Case Studies and Testimonials (first tile / left side)
• c) Certifications and Professional Memberships (third tile / right side) (This should include logos of the relevant organisations being displayed. Specifically GQT and the Pillar Seal GQT).
• - Design logo to be used from previous SketchNestle project. Example of logo attached below, please access full JPG files from our account.
Nice to have
• Sleek and modern feel.
• Approachable in terms of how people can contact the company for a quote.
• Traditional pictures to give credibility and comfort around choosing this company.
Should not have
• Cheesy pictures
• Over-complicated
• Simple to use
• Easy URL domain name

```html
<!DOCTYPE html>
<html lang="en">
<head>
<meta charset="utf-8">
<title>Marlow Brick Construction Ltd</title>
<link rel="stylesheet" href="https://fonts.googleapis.com/css2?family=Jost:wght@400;500&family=Saira:wght@500;600&display=swap">
<style>
:root{
  --brand-blue:#1457a6;
  --footer-blue:#1456a3;
  --ink:#1d1d1d;
  --white:#fff;
  --grey:#8a8a8a;
  --grey-dark:#6f6f6f;
  --badge-neutral:#d9d9d9;
  --badge-neutral-dark:#bdbdbd;
}
*{margin:0;padding:0;box-sizing:border-box}
html,body{width:1152px;height:1200px;overflow:hidden;background:var(--white)}
body{position:relative;font-family:"Jost",sans-serif;color:var(--ink)}
.brand{display:flex;align-items:center;gap:10px;position:absolute}
.brand-mark{width:18px;height:18px;background:var(--brand-blue)}
.brand-name{font-family:"Jost",sans-serif;font-weight:500;font-size:34px;color:var(--brand-blue);letter-spacing:.5px}

.site-header{position:absolute;left:0;top:0;width:1152px;height:102px}
.site-header .brand{left:156px;top:30px}
.contact-item{position:absolute;display:flex;align-items:center;gap:8px;font-size:14px;line-height:20px;color:#333}
.contact-icon{width:36px;height:36px;border-radius:50%;background:var(--brand-blue);display:flex;align-items:center;justify-content:center;flex:none}
.header-phone{left:608px;top:30px}
.header-email{left:786px;top:29px}

.hero{position:absolute;left:0;top:102px;width:1152px;height:460px;overflow:hidden}
.hero-photo{position:absolute;inset:0;background:linear-gradient(180deg,#2d3a26 0%,#3f5330 28%,#5b3a2c 50%,#6a3a2a 72%,#4a4340 100%)}
.hero-shade{position:absolute;inset:0;background:rgba(0,0,0,.28)}
.hero-content{position:absolute;left:0;top:136px;width:1152px;text-align:center;color:var(--white);font-family:"Saira",sans-serif}
.hero-title{font-weight:500;font-size:26px;line-height:31px}
.service-list{list-style:none;margin-top:20px;font-size:19px;font-weight:500;line-height:22px}
.service-list li{display:inline-block;margin:0 14px}
.service-list li::before{content:"•";margin-right:20px}
.hero-cta{display:inline-block;margin-top:24px;background:var(--brand-blue);color:var(--white);text-decoration:none;font-family:"Jost",sans-serif;font-size:16px;padding:4px 10px;height:32px;line-height:24px}

.intro{position:absolute;left:0;top:608px;width:1152px;text-align:center}
.intro .brand{position:static;justify-content:center}
.intro .brand-name{font-size:28px}
.intro-text{width:840px;margin:16px auto 0;font-size:15px;line-height:23px}
.intro-note{margin-top:8px;font-size:15px}

.tiles{position:absolute;top:816px;left:156px;display:flex;gap:21px}
.tile{position:relative;width:266px;height:183px;display:block;color:var(--white);text-decoration:none;box-shadow:0 8px 8px -4px rgba(0,0,0,.35)}
.tile-photo{position:absolute;inset:0}
.tile-case .tile-photo{background:linear-gradient(160deg,#4a4a4a,#262626)}
.tile-quote .tile-photo{background:linear-gradient(160deg,#3b3a37,#1e1e1f)}
.tile-cert .tile-photo{background:linear-gradient(160deg,#5a3e33,#3b2a25)}
.tile-icon{position:absolute;left:0;right:0;top:40px;display:flex;justify-content:center;gap:8px}
.tile-label{position:absolute;left:0;right:0;top:110px;text-align:center;font-family:"Saira",sans-serif;font-weight:500;font-size:14px;line-height:18px}
.badge{width:38px;height:50px;border-radius:4px;background:var(--badge-neutral)}
.badge-b{background:var(--badge-neutral-dark)}

.site-footer{position:absolute;left:0;top:1066px;width:1152px;height:134px;background:var(--footer-blue);color:var(--white)}
.footer-brand-panel{position:absolute;left:0;top:0;width:300px;height:134px;background:linear-gradient(180deg,var(--grey),var(--grey-dark))}
.footer-brand-panel .brand{left:60px;top:74px}
.footer-brand-panel .brand-mark{background:var(--white)}
.footer-brand-panel .brand-name{color:var(--white);font-size:24px}
.footer-item{position:absolute;display:flex;align-items:center;gap:12px;font-size:14px;line-height:21px}
.footer-item .contact-icon{background:rgba(255,255,255,.3)}
.footer-address{left:348px;top:30px}
.footer-phone{left:590px;top:31px}
.footer-email{left:780px;top:30px}
.copyright{position:absolute;left:348px;top:100px;font-size:14px}
.social{position:absolute;left:790px;top:96px;display:flex;gap:4px;list-style:none}
.social li{width:24px;height:24px;border-radius:50%;background:var(--white)}
</style>
</head>
<body>

<header class="site-header">
  <div class="brand"><span class="brand-mark"></span><span class="brand-name">Marlow Brick</span></div>
  <div class="contact-item header-phone">
    <span class="contact-icon"><svg width="18" height="18" viewBox="0 0 24 24"><path fill="#fff" d="M6.6 10.8a15.1 15.1 0 0 0 6.6 6.6l2.2-2.2c.3-.3.7-.4 1-.2 1.1.4 2.3.6 3.6.6.6 0 1 .4 1 1V20c0 .6-.4 1-1 1A17 17 0 0 1 3 4c0-.6.4-1 1-1h3.5c.6 0 1 .4 1 1 0 1.3.2 2.5.6 3.6.1.3 0 .7-.2 1z"/></svg></span>
    <span>Call Us On :<br>0161.555.0142</span>
  </div>
  <div class="contact-item header-email">
    <span class="contact-icon"><svg width="20" height="16" viewBox="0 0 20 16"><rect x="1" y="1" width="18" height="14" fill="none" stroke="#fff" stroke-width="1.6"/><path d="M1 1l9 8 9-8M1 15l6-6M19 15l-6-6" fill="none" stroke="#fff" stroke-width="1.4"/></svg></span>
    <span>Email<br>hello@marlowbrick.co.uk</span>
  </div>
</header>

<section class="hero">
  <div class="hero-photo" role="img" aria-label="Brick garden walls with pillars and a wrought iron gate over a block-paved driveway"></div>
  <div class="hero-shade"></div>
  <div class="hero-content">
    <h1 class="hero-title">Marlow Brick Construction Ltd is a construction company that<br>has expertise and experience in the following areas</h1>
    <ul class="service-list">
      <li>Extensions</li><li>New build / New houses</li><li>Garden walls</li><br>
      <li>Plastering</li><li>Brickwork</li><li>Groundworks</li>
    </ul>
    <a class="hero-cta" href="#quote">Contact Us Today &#8594;</a>
  </div>
</section>

<section class="intro">
  <div class="brand"><span class="brand-mark"></span><span class="brand-name">Marlow Brick</span></div>
  <p class="intro-text">We pride ourselves on attention to detail, pride in our completed project and client satisfaction. We believe in full transparency and this is reflected in the jobs we quote for you. We break down each step with both labour and materials cost so you can see exactly what you are paying for.</p>
  <p class="intro-note">Feel free to get in touch and we can talk through what you are looking to achieve.</p>
</section>

<nav class="tiles">
  <a class="tile tile-case" href="#case-studies">
    <div class="tile-photo" role="img" aria-label="Person reviewing documents at a desk"></div>
    <div class="tile-icon"><svg width="70" height="60" viewBox="0 0 70 60" fill="none" stroke="#fff" stroke-width="3"><rect x="30" y="2" width="36" height="54" rx="3"/><path d="M37 20h16M37 28h12M37 36h10"/><circle cx="54" cy="38" r="7"/><path d="M59 43l7 7"/><rect x="2" y="30" width="20" height="14" rx="7"/></svg></div>
    <div class="tile-label">Case Studies and<br>Testimonials</div>
  </a>
  <a class="tile tile-quote" href="#quote" id="quote">
    <div class="tile-photo" role="img" aria-label="Laptop on a desk with paperwork"></div>
    <div class="tile-icon"><svg width="56" height="60" viewBox="0 0 56 60" fill="none" stroke="#fff" stroke-width="3.5"><path d="M10 2h30l12 12v42H10z"/><path d="M22 20h18M26 30h18M30 40h14"/><path d="M2 38l8 12 12-22"/></svg></div>
    <div class="tile-label">Contact Us For A<br>Free Quote</div>
  </a>
  <a class="tile tile-cert" href="#certifications">
    <div class="tile-photo" role="img" aria-label="Bricklayer laying bricks with mortar"></div>
    <div class="tile-icon"><span class="badge" role="img" aria-label="Membership badge placeholder"></span><span class="badge badge-b" role="img" aria-label="Pillar Seal GQT badge placeholder"></span></div>
    <div class="tile-label">Certifications and Professional<br>Memberships</div>
  </a>
</nav>

<footer class="site-footer">
  <div class="footer-brand-panel">
    <div class="brand"><span class="brand-mark"></span><span class="brand-name">Marlow Brick</span></div>
  </div>
  <div class="footer-item footer-address">
    <span class="contact-icon"><svg width="14" height="20" viewBox="0 0 14 20"><path fill="#fff" d="M7 0a7 7 0 0 0-7 7c0 5 7 13 7 13s7-8 7-13a7 7 0 0 0-7-7zm0 9.5A2.5 2.5 0 1 1 7 4.5a2.5 2.5 0 0 1 0 5z"/></svg></span>
    <span>Street Name, City Name<br>State Zipcode</span>
  </div>
  <div class="footer-item footer-phone">
    <span class="contact-icon"><svg width="18" height="18" viewBox="0 0 24 24"><path fill="#fff" d="M6.6 10.8a15.1 15.1 0 0 0 6.6 6.6l2.2-2.2c.3-.3.7-.4 1-.2 1.1.4 2.3.6 3.6.6.6 0 1 .4 1 1V20c0 .6-.4 1-1 1A17 17 0 0 1 3 4c0-.6.4-1 1-1h3.5c.6 0 1 .4 1 1 0 1.3.2 2.5.6 3.6.1.3 0 .7-.2 1z"/></svg></span>
    <span>Call Us On :<br>0161.555.0142</span>
  </div>
  <div class="footer-item footer-email">
    <span class="contact-icon"><svg width="20" height="16" viewBox="0 0 20 16"><rect x="1" y="1" width="18" height="14" fill="none" stroke="#fff" stroke-width="1.6"/><path d="M1 1l9 8 9-8M1 15l6-6M19 15l-6-6" fill="none" stroke="#fff" stroke-width="1.4"/></svg></span>
    <span>Email<br>hello@marlowbrick.co.uk</span>
  </div>
  <p class="copyright">Copyright ©2018 Marlow Brick Construction Ltd. All Rights Reserved.</p>
  <ul class="social" aria-label="Social links">
    <li></li><li></li><li></li><li></li>
  </ul>
</footer>

</body>
</html>
```